Smack you in the face - Landing page for Residential Electrical Repairs (Searchly Ads)

I need an effective landing page for Searchly ads. The ads will target residential electrical repairs. Lighting Outages, Power Outages, Breakers Tripping, Outlets Not Working. I need a strong call to action to Call Us Now! Forms don't work well for us so we only need one form as a last option at the bottom of the page. We only work on homes. the website is https://www.vantor-wiring.example/
email is : support@vantor-wiring.example
Phone 555-217-4086

**This is about one focused service. Electrical Repairs - That includes Partial Power Outages, Outlets Not Working, Tripped Breakers, Electrical Panel repairs, and Fusebox Repairs. The area served will only be Greenville, SC. KOBA is the platform

Target Market(s)

Homeonwers in need of electrical repair

Industry/Entity Type

Residential Electricians

Coding

Coded - Design and coding required

Requirements
Must have
• Strong to action for phone calls, this landing page must grab action fast.
Nice to have
• Social proof with existing 5 start reviews for Searchly, Rately, TCB, and Friendnet
Should not have
• Should not be form based. I do not like the site's current them, please don't copy it. Make your own.

```html
<!DOCTYPE html>
<html lang="en">
<head>
<meta charset="utf-8">
<title>Vantor Wiring – Residential Electrical Repairs in Greenville, SC</title>
<link href="https://fonts.googleapis.com/css2?family=Michroma&family=Montserrat:wght@400;500;600;700;800&display=swap" rel="stylesheet">
<style>
:root{
  --blue:#2a9ad6;
  --blue-deep:#1f86c0;
  --blue-panel:#1b78ad;
  --orange:#f0a31a;
  --ink:#111111;
  --navy:#14294a;
  --text:#333333;
  --muted:#777777;
  --light:#f2f8fc;
  --white:#ffffff;
  --star:#f5b51c;
}
*{box-sizing:border-box;margin:0;padding:0}
html,body{width:1200px;height:4418px;overflow:hidden}
body{font-family:"Montserrat",sans-serif;color:var(--text);background:var(--white);position:relative}
.abs{position:absolute}
.display{font-family:"Michroma",sans-serif;text-transform:uppercase;letter-spacing:1px;color:var(--ink);font-weight:400}
.btn{position:absolute;background:var(--orange);color:var(--white);font-weight:700;font-size:16px;border-radius:26px;display:flex;align-items:center;justify-content:center}
.stars{color:var(--star);letter-spacing:1px}

/* header */
.site-header{position:absolute;top:0;left:0;width:1200px;height:128px;background:var(--light)}
.topbar{position:absolute;left:400px;top:0;width:800px;height:40px;background:var(--blue);clip-path:polygon(0 0,100% 0,100% 100%,28px 100%)}
.topbar-item{position:absolute;top:11px;color:var(--white);font-size:14px;font-weight:600;display:flex;align-items:center;gap:6px}
.logo{position:absolute;left:128px;top:36px;width:226px;text-align:center}
.logo-name{display:block;font-weight:800;font-size:29px;color:var(--navy);letter-spacing:1px;line-height:34px}
.logo-tag{display:block;font-weight:600;font-size:12px;color:var(--blue);letter-spacing:3px;line-height:18px}
.main-nav{position:absolute;left:459px;top:76px;width:626px;display:flex;justify-content:space-between;font-size:15px;font-weight:600;color:var(--ink)}

/* hero */
.hero{position:absolute;top:128px;left:0;width:1200px;height:582px;background:linear-gradient(90deg,#3b3b3b 0%,#4a4a4a 45%,#6f6a66 70%,#8a6a4c 100%)}
.hero-title{position:absolute;left:112px;top:106px;font-size:28px;line-height:42px;color:var(--white);font-weight:400;-webkit-text-stroke:1px var(--white)}
.hero-sub{position:absolute;left:110px;top:286px;font-size:16px;line-height:27px;color:var(--white);font-weight:600}
.badge{position:absolute;top:462px;width:112px;height:70px;background:var(--white);border-radius:9px;display:flex;align-items:flex-end;justify-content:center;padding-bottom:10px;font-size:16px}

/* services */
.services-title{position:absolute;top:804px;width:1200px;text-align:center;font-size:38px;-webkit-text-stroke:1px var(--ink)}
.section-lead{position:absolute;top:866px;width:1200px;text-align:center;font-size:14px;line-height:26px;color:var(--muted)}
.service-card{position:absolute;top:951px;width:308px;height:388px;border-radius:10px;overflow:hidden}
.service-photo{position:absolute;inset:0}
.service-label{position:absolute;left:0;bottom:0;width:100%;height:78px;background:rgba(42,154,214,.88);color:var(--white);font-size:23px;font-weight:600;display:flex;align-items:center;justify-content:center}
.arrow{position:absolute;width:28px;height:28px;border-radius:50%;display:flex;align-items:center;justify-content:center}
.arrow.prev{background:#555}
.arrow.next{background:var(--blue)}

/* about */
.about{position:absolute;top:1432px;left:0;width:1200px;height:574px;background:linear-gradient(120deg,#2796d3,#1c86c3)}
.about-frame{position:absolute;left:100px;top:98px;width:474px;height:382px;border:4px solid rgba(255,255,255,.35);border-radius:10px}
.about-photo{position:absolute;left:129px;top:122px;width:406px;height:328px;border-radius:10px;background:linear-gradient(135deg,#7a4f33,#2e5f9a 55%,#c9c9c9)}
.about-title{position:absolute;left:600px;top:92px;font-size:38px;color:var(--white);-webkit-text-stroke:1px var(--white)}
.about-text{position:absolute;left:601px;top:150px;width:370px;font-size:14px;line-height:25.7px;color:var(--white)}

/* common repairs */
.repairs-title{position:absolute;top:2096px;width:1200px;text-align:center;font-size:38px;-webkit-text-stroke:1px var(--ink)}
.repair-card{position:absolute;top:2176px;height:384px;background:var(--white);box-shadow:0 2px 10px rgba(0,0,0,.12);border-radius:4px;overflow:hidden}
.repair-photo{position:absolute;left:4px;top:4px;right:4px;border-radius:4px}
.repair-card h3{position:absolute;font-weight:600;color:var(--ink)}
.repair-tag{position:absolute;font-size:13px;color:var(--blue);font-weight:600;display:flex;align-items:center;gap:6px}
.repair-excerpt{position:absolute;font-size:13px;line-height:27px;color:#444}
.read-more{position:absolute;font-size:14px;font-weight:700;color:var(--blue);text-decoration:underline}

/* reviews */
.reviews-title{position:absolute;top:2720px;width:1200px;text-align:center;font-size:38px;-webkit-text-stroke:1px var(--ink)}
.reviews-total{position:absolute;top:2802px;width:1200px;text-align:center;font-size:23px;font-weight:600;color:var(--ink)}
.reviews-score{position:absolute;top:2842px;width:1200px;text-align:center;font-size:22px;font-weight:700;color:var(--ink)}
.review-card{position:absolute;top:2935px;width:314px;height:315px;background:var(--white);box-shadow:0 2px 12px rgba(0,0,0,.12);border-radius:6px}
.avatar{position:absolute;left:12px;top:16px;width:72px;height:72px;border-radius:50%;background:linear-gradient(#d9c7b5,#9a7a60)}
.reviewer{position:absolute;left:94px;top:30px;font-size:17px;font-weight:600;color:var(--ink);line-height:24px}
.review-date{position:absolute;left:94px;font-size:13px;color:var(--ink)}
.source-dot{position:absolute;right:16px;top:28px;width:38px;height:38px;border-radius:50%;border:5px solid #3b82f6}
.review-stars{position:absolute;left:14px;top:112px;font-size:28px}
.review-text{position:absolute;left:16px;top:164px;width:284px;font-size:13.5px;line-height:27.5px;color:#555}

/* contact */
.contact{position:absolute;top:3339px;left:0;width:1200px;height:729px;background:var(--blue)}
.form-panel{position:absolute;left:109px;top:78px;width:481px;height:583px;background:var(--blue-panel);border-radius:6px}
.form-title{position:absolute;top:44px;width:100%;text-align:center;font-size:24px;line-height:47px;color:var(--white);-webkit-text-stroke:.6px var(--white)}
.field{position:absolute;left:27px;width:431px;height:50px;border:2px solid rgba(255,255,255,.8);border-radius:6px;color:var(--white);font-size:13px;padding:14px 14px}
.contact-title{position:absolute;left:618px;top:88px;font-size:36px;color:var(--white);-webkit-text-stroke:1px var(--white)}
.contact-sub{position:absolute;left:618px;top:158px;font-size:21px;font-weight:600;color:var(--white)}
.contact-line{position:absolute;color:var(--white);font-size:14px;font-weight:600;line-height:23px}
.icon-circle{position:absolute;width:38px;height:38px;border-radius:50%;background:var(--white);display:flex;align-items:center;justify-content:center}
.map{position:absolute;left:618px;top:303px;width:454px;height:331px;border-radius:12px;background:linear-gradient(135deg,#f4f3ef,#e6eaee)}

/* footer */
.site-footer{position:absolute;top:4068px;left:0;width:1200px;height:350px;background:#050505;color:var(--white)}
.footer-logo{position:absolute;left:108px;top:90px;width:224px;text-align:center}
.footer-logo .logo-name{color:var(--white);font-size:26px}
.footer-logo .logo-tag{color:var(--white)}
.footer-social{position:absolute;left:108px;top:248px;width:224px;display:flex;justify-content:center;gap:16px;font-size:13px;font-weight:600}
.footer-col{position:absolute;top:88px}
.footer-col h4{font-size:22px;font-weight:600;margin-bottom:14px}
.footer-col li{list-style:none;font-size:15px;line-height:30px}
.footer-rule{position:absolute;left:108px;top:286px;width:980px;height:1px;background:#555}
.copyright{position:absolute;top:312px;width:1200px;text-align:center;font-size:13px}
</style>
</head>
<body>

<header class="site-header">
  <div class="topbar">
    <div class="topbar-item" style="left:74px">
      <svg width="14" height="14" viewBox="0 0 24 24"><path fill="#fff" d="M6.6 10.8c1.4 2.8 3.8 5.1 6.6 6.6l2.2-2.2c.3-.3.7-.4 1-.2 1.1.4 2.3.6 3.6.6.6 0 1 .4 1 1V20c0 .6-.4 1-1 1C10.6 21 3 13.4 3 4c0-.6.4-1 1-1h3.5c.6 0 1 .4 1 1 0 1.3.2 2.5.6 3.6.1.3 0 .7-.2 1z"/></svg>
      (555) 217-4086
    </div>
    <div class="topbar-item" style="left:334px">
      <svg width="12" height="15" viewBox="0 0 24 30"><path fill="#fff" d="M12 0C5.4 0 0 5.4 0 12c0 9 12 18 12 18s12-9 12-18C24 5.4 18.6 0 12 0zm0 16a4 4 0 110-8 4 4 0 010 8z"/></svg>
      218 Larkspur Ave, STE 4 Greenville, SC 29615
    </div>
  </div>
  <div class="logo"><span class="logo-name">VANTOR</span><span class="logo-tag">WIRING · REPAIRS</span></div>
  <nav class="main-nav">
    <span>Home</span><span>Repairs</span><span>Breakers</span><span>Outlets</span><span>Panels</span><span>Reviews</span><span>Call Now</span>
  </nav>
</header>

<section class="hero">
  <div class="abs" style="inset:0" role="img" aria-label="Electrician in a hard hat and orange safety vest repairing a home electrical panel"></div>
  <h1 class="display hero-title">Power Out?<br>Breaker Tripping?<br>Call Us Now<br>For Repairs</h1>
  <p class="hero-sub">Outlets, Breakers, Panels &amp; Fusebox Repairs<br>Homes Only · Serving Greenville, SC</p>
  <div class="btn" style="left:112px;top:366px;width:196px;height:46px">Call Us Now</div>
  <div class="badge" style="left:112px" role="img" aria-label="Searchly five-star rating"><span class="stars">★★★★★</span></div>
  <div class="badge" style="left:232px" role="img" aria-label="Rately five-star rating"><span class="stars">★★★★★</span></div>
  <div class="badge" style="left:352px" role="img" aria-label="TCB five-star rating"><span class="stars">★★★★★</span></div>
  <div class="badge" style="left:472px" role="img" aria-label="Friendnet five-star rating"><span class="stars">★★★★★</span></div>
</section>

<section class="services">
  <h2 class="display services-title">Our Services</h2>
  <p class="section-lead">One focus: fixing the electrical problems in your home. Partial power outages, dead<br>outlets, tripped breakers and panel faults in Greenville, SC. Call (555) 217-4086.</p>
  <div class="arrow prev" style="left:16px;top:1135px"><svg width="10" height="12" viewBox="0 0 10 12"><path d="M7 1L2 6l5 5" stroke="#fff" stroke-width="2" fill="none"/></svg></div>
  <div class="service-card" style="left:106px">
    <div class="service-photo" role="img" aria-label="Electrician repairing a wall unit in a home" style="background:linear-gradient(135deg,#e6e6e6,#b9c3cc 50%,#2f5fa8)"></div>
    <div class="service-label">Electrical Repairs</div>
  </div>
  <div class="service-card" style="left:440px">
    <div class="service-photo" role="img" aria-label="Row of circuit breakers in a panel" style="background:linear-gradient(160deg,#cfd8e2,#8a9aa8 50%,#e2c23a)"></div>
    <div class="service-label">Lighting Outages</div>
  </div>
  <div class="service-card" style="left:776px">
    <div class="service-photo" role="img" aria-label="Home electrical board with main switch" style="background:linear-gradient(160deg,#3a6fb0,#c9ccd0 50%,#7b8590)"></div>
    <div class="service-label">Power Outages</div>
  </div>
  <div class="arrow next" style="left:1158px;top:1135px"><svg width="10" height="12" viewBox="0 0 10 12"><path d="M3 1l5 5-5 5" stroke="#fff" stroke-width="2" fill="none"/></svg></div>
</section>

<section class="about">
  <div class="about-frame"></div>
  <div class="about-photo" role="img" aria-label="Hand using a screwdriver on breaker wiring"></div>
  <h2 class="display about-title">About Us</h2>
  <p class="about-text">Vantor Wiring is a residential repair team serving Greenville, SC homeowners only. When half the house goes dark, an outlet stops working or a breaker will not stay on, we send a licensed electrician who finds the fault and fixes it the same visit. We repair panels and old fuseboxes, trace partial outages and replace failed breakers safely. No sales pitch, no guessing, just honest repairs with clear upfront pricing. Skip the forms and call us now for fast help.</p>
  <div class="btn" style="left:596px;top:436px;width:195px;height:44px">Call Us Now</div>
</section>

<section class="repairs">
  <h2 class="display repairs-title">Common Repairs</h2>
  <article class="repair-card" style="left:102px;width:478px">
    <div class="repair-photo" role="img" aria-label="Electrician tracing wiring along a ceiling" style="height:246px;background:linear-gradient(135deg,#9a9a9a,#e4e4e4 60%,#6d6d6d)"></div>
    <h3 style="left:16px;top:266px;font-size:23px;line-height:31px">Partial Power Outage in<br>Your Home</h3>
    <div class="repair-tag" style="left:16px;top:342px;font-size:15px"><svg width="20" height="20" viewBox="0 0 20 20"><path d="M4 10l4 4 8-8" stroke="#2a9ad6" stroke-width="2" fill="none"/></svg>Same-Day Repair</div>
  </article>
  <article class="repair-card" style="left:593px;width:245px">
    <div class="repair-photo" role="img" aria-label="Tripped circuit breakers close-up" style="height:184px;background:linear-gradient(160deg,#3a6fb0,#cdd3d8 55%,#d04a2a)"></div>
    <h3 style="left:14px;top:196px;font-size:14.5px;line-height:27px">Breakers Tripping or<br>Outlets Not Working</h3>
    <div class="repair-tag" style="left:14px;top:262px"><svg width="16" height="16" viewBox="0 0 20 20"><path d="M4 10l4 4 8-8" stroke="#2a9ad6" stroke-width="2" fill="none"/></svg>Homes Only</div>
    <p class="repair-excerpt" style="left:14px;top:286px;width:220px">Dead outlets or breakers that<br>won't reset? We find the fault.</p>
    <span class="read-more" style="left:14px;top:346px">Call Now...</span>
  </article>
  <article class="repair-card" style="left:849px;width:245px">
    <div class="repair-photo" role="img" aria-label="Person checking an old fuse box with a lantern" style="height:184px;background:linear-gradient(160deg,#1c1c1c,#4a4a4a 60%,#9aa0a6)"></div>
    <h3 style="left:14px;top:196px;font-size:14.5px;line-height:27px">Electrical Panel &amp;<br>Fusebox Repairs</h3>
    <div class="repair-tag" style="left:14px;top:262px"><svg width="16" height="16" viewBox="0 0 20 20"><path d="M4 10l4 4 8-8" stroke="#2a9ad6" stroke-width="2" fill="none"/></svg>Greenville, SC</div>
    <p class="repair-excerpt" style="left:14px;top:286px;width:225px">Burnt, buzzing or failing panel?<br>Licensed repair, done safely.</p>
    <span class="read-more" style="left:14px;top:346px">Call Now...</span>
  </article>
  <div class="btn" style="left:501px;top:2614px;width:196px;height:46px">Call Us Now</div>
</section>

<section class="reviews">
  <h2 class="display reviews-title">What Our Clients Say</h2>
  <p class="reviews-total">270 Total Reviews</p>
  <p class="reviews-score"><span class="stars" style="font-size:36px;vertical-align:middle">★★★★★</span> <span style="vertical-align:middle">4.9</span></p>
  <div class="arrow prev" style="left:16px;top:3088px"><svg width="10" height="12" viewBox="0 0 10 12"><path d="M7 1L2 6l5 5" stroke="#fff" stroke-width="2" fill="none"/></svg></div>
  <article class="review-card" style="left:106px">
    <div class="avatar" role="img" aria-label="Reviewer portrait"></div>
    <p class="reviewer">Maren<br>Holloway</p>
    <p class="review-date" style="top:80px">10.03.2023</p>
    <div class="source-dot" role="img" aria-label="Searchly review"></div>
    <div class="review-stars stars">★★★★★</div>
    <p class="review-text">Theo and Rafe were excellent in finding the problem. I appreciate their professionalism, patience, and problem solving skills! You have earned a trusted customer!</p>
  </article>
  <article class="review-card" style="left:440px">
    <div class="avatar" role="img" aria-label="Reviewer portrait"></div>
    <p class="reviewer">Celia Brandt</p>
    <p class="review-date" style="top:62px">09.30.2023</p>
    <div class="source-dot" role="img" aria-label="Searchly review"></div>
    <div class="review-stars stars">★★★★★</div>
    <p class="review-text">Searched to find an electrician and WES from Ridgeline electric responded. He was very friendly, professional and showed interest in my dilemma. He</p>
    <span class="read-more" style="left:16px;top:266px">Read More..</span>
  </article>
  <article class="review-card" style="left:773px">
    <div class="avatar" role="img" aria-label="Reviewer portrait"></div>
    <p class="reviewer">Odette Ruiz</p>
    <p class="review-date" style="top:62px">10.16.2023</p>
    <div class="source-dot" role="img" aria-label="Searchly review"></div>
    <div class="review-stars stars">★★★★★</div>
    <p class="review-text">Theo was wonderful and immediately identified what was tripping an electrical breaker box out by our pool. He then installed an outlet</p>
    <span class="read-more" style="left:16px;top:266px">Read More..</span>
  </article>
  <div class="arrow next" style="left:1158px;top:3088px"><svg width="10" height="12" viewBox="0 0 10 12"><path d="M3 1l5 5-5 5" stroke="#fff" stroke-width="2" fill="none"/></svg></div>
</section>

<section class="contact">
  <form class="form-panel">
    <h2 class="display form-title">Your Electrical<br>Needs, Our Expertise</h2>
    <div class="field" style="top:146px">Your Name</div>
    <div class="field" style="top:205px">Email Address</div>
    <div class="field" style="top:265px">Phone Number</div>
    <div class="field" style="top:326px;height:107px">Message</div>
    <div class="btn" style="left:159px;top:465px;width:162px;height:44px">Send Message</div>
  </form>
  <h2 class="display contact-title">Contact Us</h2>
  <p class="contact-sub">Greenville, SC Location</p>
  <div class="icon-circle" style="left:620px;top:206px"><svg width="14" height="18" viewBox="0 0 24 30"><path fill="#1b78ad" d="M12 0C5.4 0 0 5.4 0 12c0 9 12 18 12 18s12-9 12-18C24 5.4 18.6 0 12 0zm0 16a4 4 0 110-8 4 4 0 010 8z"/></svg></div>
  <p class="contact-line" style="left:668px;top:208px">218 Larkspur Ave<br>Suite 4<br>Greenville, SC 29615</p>
  <div class="icon-circle" style="left:870px;top:206px"><svg width="16" height="16" viewBox="0 0 24 24"><path fill="#1b78ad" d="M6.6 10.8c1.4 2.8 3.8 5.1 6.6 6.6l2.2-2.2c.3-.3.7-.4 1-.2 1.1.4 2.3.6 3.6.6.6 0 1 .4 1 1V20c0 .6-.4 1-1 1C10.6 21 3 13.4 3 4c0-.6.4-1 1-1h3.5c.6 0 1 .4 1 1 0 1.3.2 2.5.6 3.6.1.3 0 .7-.2 1z"/></svg></div>
  <p class="contact-line" style="left:918px;top:214px">(555) 217-4086</p>
  <div class="map" role="img" aria-label="Street map of the Greenville, SC office location"></div>
</section>

<footer class="site-footer">
  <div class="footer-logo"><span class="logo-name">VANTOR</span><span class="logo-tag">WIRING · REPAIRS</span></div>
  <div class="footer-social"><span>Friendnet</span><span>Chirp</span><span>Linkup</span></div>
  <div class="footer-col" style="left:393px">
    <h4>Quick Links</h4>
    <ul><li>Home</li><li>Repairs</li><li>Reviews</li><li>Call Now</li></ul>
  </div>
  <div class="footer-col" style="left:618px">
    <h4>Other Links</h4>
    <ul><li>Breakers</li><li>Outlets</li><li>Panels</li></ul>
  </div>
  <div class="footer-col" style="left:845px">
    <h4>Greenville, SC Location</h4>
    <ul><li>218 Larkspur Ave</li><li style="padding-left:18px">Suite 4</li><li style="padding-left:18px">Greenville, SC 29615</li><li>(555) 217-4086</li></ul>
  </div>
  <div class="footer-rule"></div>
  <p class="copyright">© 2023 Vantor Wiring .All rights reserved · support@vantor-wiring.example</p>
</footer>

</body>
</html>
```